Business card design for holistic health care clinic

We need a double-sided business card design for our holistic health care clinic that integrates our logo design and also its color scheme. My business is called Valmira. It is an integrative medicine clinic. You have already done the logo for me. Please ensure an elegant and upscale design that is not cluttered, but still has all the necessary information (please see below for details).

Target Market(s)

Wellness, fitness, rehabilitation for educated, well-traveled open-minded clients who are focused on natural, organic, balanced and preventive healthcare and lifestyle.

Industry/Entity Type

Medical

Contact Information for Business Card

Modern, clean.

Number of Pages Required

1 page

Font styles to use
Serif
Sans Serif

Colors

Designer to choose colors to be used in the design.

Requirements
Must have
• Logo on one side, all other information on the other side.
• Other information should include:
• Tobias Wrenfeld - DOE, CPT, LMT
• 4100 East Marrow Drive
• Austin, TX 78119
• 512 555 0148
• 818 555 0192
• info@ValmiraHealth.example
• t.wrenfeld@ValmiraHealth.example
Nice to have
• Darker background on front - but not totally black - shaded/dark gray.

```html
<!DOCTYPE html>
<html lang="en">
<head>
<meta charset="utf-8">
<title>Valmira – Business Card</title>
<link rel="stylesheet" href="https://fonts.googleapis.com/css2?family=Nunito:wght@800&family=Roboto:wght@400&family=Roboto+Condensed:wght@700&display=swap">
<style>
  :root {
    --backdrop: #5e4330;
    --card-dark-top: #303031;
    --card-dark-bottom: #232324;
    --brand-blue: #1a8dcc;
    --card-blue: #1e92d0;
    --ink-dark: #232323;
    --text-light: #e6e6e6;
    --band-grey: #b9b9b9;
  }
  * { margin: 0; padding: 0; box-sizing: border-box; }
  html, body { width: 1200px; height: 960px; overflow: hidden; }
  body { background: var(--backdrop); position: relative; }

  .card { position: absolute; border-radius: 22px; overflow: hidden; box-shadow: 0 3px 8px rgba(0,0,0,.45); }

  /* Front: contact side */
  .card--front {
    left: 315px; top: 113px; width: 597px; height: 342px;
    background: linear-gradient(180deg, var(--card-dark-top), var(--card-dark-bottom));
  }
  .wordmark {
    position: absolute; font-family: "Nunito", sans-serif; font-weight: 800;
    letter-spacing: 1px; line-height: 1; white-space: nowrap;
  }
  .card--front .wordmark {
    left: 173px; top: 186px; transform: translate(-50%, -50%);
    font-size: 46px; color: var(--brand-blue);
  }
  .divider {
    position: absolute; left: 312px; top: 98px; width: 2px; height: 164px;
    background: linear-gradient(180deg, transparent, rgba(255,255,255,.7) 50%, transparent);
  }
  .contact { position: absolute; left: 336px; top: 102px; font-family: "Roboto", sans-serif; color: var(--text-light); }
  .contact__name {
    font-family: "Roboto Condensed", sans-serif; font-weight: 700; font-size: 19px;
    color: var(--brand-blue); letter-spacing: .2px; white-space: nowrap;
  }
  .contact__credentials { font-size: 12px; }
  .contact__address { margin-top: 16px; font-size: 14.5px; line-height: 18px; }
  .contact__list { list-style: none; margin-top: 11px; font-size: 14.5px; line-height: 19px; }
  .contact__list li { display: flex; align-items: center; gap: 9px; white-space: nowrap; }
  .contact__list svg { width: 13px; height: 13px; fill: var(--brand-blue); flex: none; }

  .edge-band { position: absolute; left: 0; bottom: 0; width: 100%; height: 12px; }
  .edge-band__blue { position: absolute; left: 0; top: 0; height: 100%; width: 394px; background: var(--brand-blue); clip-path: polygon(0 0, 100% 0, 99% 100%, 0 100%); }
  .edge-band__grey { position: absolute; left: 393px; top: 0; height: 100%; right: 0; background: var(--band-grey); clip-path: polygon(1.5% 0, 100% 0, 100% 100%, 0 100%); }

  /* Back: logo side */
  .card--back {
    left: 312px; top: 472px; width: 598px; height: 341px;
    background: var(--card-blue);
  }
  .card--back .wordmark {
    left: 300px; top: 172px; transform: translate(-50%, -50%);
    font-size: 62px; color: var(--ink-dark);
  }
  .tagline {
    position: absolute; left: 0; right: 0; top: 281px; text-align: center;
    font-family: "Roboto", sans-serif; font-size: 14.5px; color: var(--ink-dark);
  }
</style>
</head>
<body>

<section class="card card--front" aria-label="Business card front">
  <div class="wordmark">VALMIRA</div>
  <div class="divider"></div>
  <div class="contact">
    <div class="contact__name">TOBIAS WRENFELD <span class="contact__credentials">- DOE, CPT, LMT</span></div>
    <div class="contact__address">4100 East Marrow Drive<br>Austin, TX 78119</div>
    <ul class="contact__list">
      <li><svg viewBox="0 0 24 24"><path d="M6.6 10.8a15.1 15.1 0 0 0 6.6 6.6l2.2-2.2c.3-.3.7-.4 1-.2 1.1.4 2.3.6 3.6.6.6 0 1 .4 1 1V20c0 .6-.4 1-1 1A17 17 0 0 1 3 4c0-.6.4-1 1-1h3.5c.6 0 1 .4 1 1 0 1.3.2 2.5.6 3.6.1.3 0 .7-.2 1z"/></svg>512 555 0148</li>
      <li><svg viewBox="0 0 24 24"><path d="M7 1h10a2 2 0 0 1 2 2v18a2 2 0 0 1-2 2H7a2 2 0 0 1-2-2V3a2 2 0 0 1 2-2zm0 3v14h10V4zm5 15.2a1.2 1.2 0 1 0 0 2.4 1.2 1.2 0 0 0 0-2.4z"/></svg>818 555 0192</li>
      <li><svg viewBox="0 0 24 24"><path d="M2 5h20v14H2zm2 2v.5l8 5 8-5V7zm0 3v7h16v-7l-8 5z"/></svg>t.wrenfeld@ValmiraHealth.example</li>
      <li><svg viewBox="0 0 24 24"><path d="M12 2a10 10 0 1 0 0 20 10 10 0 0 0 0-20zm-1 17.9A8 8 0 0 1 4.1 11H7v2l3 3v3.9zM18 16.4A2 2 0 0 0 16 15h-1v-3H9v-2h2V8h2V5.5A8 8 0 0 1 18 16.4z"/></svg>www.ValmiraHealth.example</li>
    </ul>
  </div>
  <div class="edge-band">
    <div class="edge-band__blue"></div>
    <div class="edge-band__grey"></div>
  </div>
</section>

<section class="card card--back" aria-label="Business card back">
  <div class="wordmark">VALMIRA</div>
  <p class="tagline">care that follows you – your pace, your wellbeing</p>
</section>

</body>
</html>
```